One Page Website for Personal Trainer in London

I have a logo and need a one page website designed around my branding. I am a freelance Personal Trainer based in London specialising in bodyweight training for men and women. I would like the site to be modern and clean but not overtly urban in design.
I need the following headings:
About Me
My Services
Events
Blog
I don't need them to be seperate pages but if they can link to further down the page that would be great.
Industry/Entity Type
Personal Trainer
Coding
Coded - Design and coding required
Number of Pages Required
1 page
Requirements
Must have
- I need the following headings:
- About Me
- My Services
- Events
- Blog
- mobile friendly formatting
- health and fitness related photography
- Colour scheme in keeping with my existing logo

```html
<!DOCTYPE html>
<html lang="en">
<head>
<meta charset="utf-8">
<title>Maren Holt Personal Training</title>
<link rel="stylesheet" href="https://fonts.googleapis.com/css2?family=Questrial&family=Poppins:wght@300;400;500;600&family=Open+Sans:wght@400;600;700&family=Playfair+Display&display=swap">
<style>
:root{
  --orange:#f7941d;
  --orange-soft:#f9a940;
  --ink:#1d1d1d;
  --text:#555;
  --white:#fff;
  --grey-panel:#5a5a5a;
}
*{box-sizing:border-box;margin:0;padding:0}
html,body{width:1200px;height:4390px;overflow:hidden}
body{position:relative;background:var(--white);font-family:"Poppins",sans-serif;color:var(--text)}
.abs{position:absolute}
a{color:inherit;text-decoration:none}

/* hero */
.hero{left:0;top:0;width:1200px;height:606px;
  background:
    radial-gradient(ellipse 150px 150px at 700px 440px,#f0506a 0%,#e8475f 60%,rgba(232,71,95,0) 100%),
    radial-gradient(ellipse 190px 90px at 820px 560px,#6b4b9a 0%,rgba(107,75,154,0) 100%),
    radial-gradient(ellipse 120px 260px at 800px 300px,rgba(214,170,140,.85) 0%,rgba(214,170,140,0) 100%),
    linear-gradient(100deg,#8f9d25 0%,#b8b935 35%,#d6c54a 60%,#a9b233 100%)}
.navbar{left:88px;top:15px;width:1024px;height:82px;background:var(--white);display:flex;align-items:center;padding:0 24px}
.brand{display:flex;align-items:center;gap:10px;font-weight:600;font-size:17px;color:var(--ink)}
.brand-mark{width:26px;height:26px;border-radius:50%;background:var(--orange)}
.nav{margin-left:auto;display:flex;gap:42px;font-size:13px;color:var(--ink);height:100%;align-items:center}
.nav a{position:relative;height:100%;display:flex;align-items:center}
.nav a.active::after{content:"";position:absolute;left:0;right:0;bottom:0;height:4px;background:var(--orange)}
.hero-kicker{left:94px;top:218px;font-family:"Questrial",sans-serif;font-size:19px;color:var(--white);letter-spacing:.5px}
.hero-title{left:94px;top:244px;font-family:"Questrial",sans-serif;font-size:62px;color:var(--white);font-weight:400}
.hero-sub{left:94px;top:328px;font-size:24px;color:var(--white);font-weight:500}
.btn{display:inline-block;background:var(--orange);color:var(--white);font-size:14px;border-radius:4px;padding:12px 22px}
.hero-btn{left:94px;top:376px}

/* about */
.about-accent{left:95px;top:980px;width:320px;height:110px;background:var(--orange);clip-path:polygon(0 0,22% 0,22% 80%,100% 80%,100% 100%,0 100%)}
.about-photo{left:117px;top:667px;width:293px;height:401px;
  background:
    radial-gradient(ellipse 40px 110px at 150px 260px,#e8d8c8 0%,rgba(232,216,200,0) 100%),
    linear-gradient(180deg,#8fc0d8 0%,#b9d5e0 12%,#4f7a45 22%,#6f8f55 34%,#3f7f98 42%,#86b6c4 58%,#c7d8d8 75%,#d8cbb0 100%)}
.about-text{left:445px;top:688px;width:580px}
.about-text h2{font-family:"Questrial",sans-serif;font-weight:400;font-size:38px;color:var(--ink)}
.about-text h3{font-size:13px;color:var(--ink);font-weight:500;margin:16px 0 14px;position:relative;padding-bottom:14px}
.about-text h3::after{content:"";position:absolute;left:0;bottom:0;width:96px;height:3px;background:var(--orange)}
.about-text p{font-size:13.5px;line-height:1.75;margin-bottom:18px}

/* headings */
.sec-title{left:0;width:1200px;text-align:center;font-family:"Questrial",sans-serif;font-size:50px;font-weight:400}
.divider{left:490px;width:220px;height:30px;display:flex;align-items:center;gap:16px}
.divider i{flex:1;height:2px;background:currentColor}
.divider b{width:24px;height:24px;border-radius:50%;border:4px solid var(--orange)}

/* features */
.features{left:0;top:1191px;width:1200px;height:574px;
  background:
    radial-gradient(ellipse 260px 200px at 300px 260px,rgba(160,90,30,.35) 0%,rgba(160,90,30,0) 100%),
    radial-gradient(ellipse 260px 220px at 900px 300px,rgba(160,90,30,.3) 0%,rgba(160,90,30,0) 100%),
    linear-gradient(180deg,var(--orange-soft),var(--orange))}
.feature{top:1350px;width:240px;text-align:center;color:var(--white)}
.feature-icon{width:150px;height:150px;margin:0 auto;border-radius:50%;background:var(--white);border:6px solid rgba(255,255,255,.55);background-clip:padding-box;display:flex;align-items:center;justify-content:center}
.feature h4{font-family:"Questrial",sans-serif;font-weight:400;font-size:19px;margin:24px 0 12px}
.feature p{font-size:12.5px;line-height:1.6;padding:0 20px}

/* trainers */
.trainer-accent{left:72px;top:2000px;width:70px;height:344px;background:var(--orange);clip-path:polygon(0 0,25% 0,25% 95%,100% 95%,100% 100%,0 100%)}
.trainer-photo{top:1982px;height:345px}
.tp1{background:radial-gradient(ellipse 120px 150px at 170px 170px,#b07a5a 0%,#6a4434 45%,rgba(30,30,30,0) 100%),radial-gradient(ellipse 90px 60px at 110px 230px,#9a9a9a 0%,rgba(90,90,90,0) 100%),linear-gradient(180deg,#262626,#111)}
.tp2{background:radial-gradient(ellipse 110px 170px at 155px 190px,#d2a07c 0%,#8a5c42 45%,rgba(30,30,30,0) 100%),linear-gradient(180deg,#4a4a4a,#1a1a1a)}
.tp3{background:radial-gradient(ellipse 80px 90px at 140px 80px,#e8cf9a 0%,rgba(232,207,154,0) 100%),radial-gradient(ellipse 120px 170px at 160px 220px,#c8977a 0%,#6a4a3e 50%,rgba(20,20,20,0) 100%),linear-gradient(180deg,#2a2a2a,#0f0f0f)}
.trainer{top:2352px;text-align:center}
.trainer h4{font-family:"Questrial",sans-serif;font-weight:400;font-size:28px;color:var(--ink)}
.trainer span{font-size:12px;color:var(--text)}

/* testimonials */
.testimonials{left:0;top:2523px;width:1200px;height:536px;
  background:radial-gradient(ellipse 300px 220px at 850px 220px,rgba(150,80,25,.3) 0%,rgba(150,80,25,0) 100%),linear-gradient(180deg,var(--orange-soft),var(--orange))}
.quote-frame{left:181px;top:2593px;width:829px;height:404px;border:5px solid var(--ink)}
.quote-title{left:390px;top:2560px;width:420px;text-align:center;background:#f9a43a;font-family:"Questrial",sans-serif;font-size:46px;color:var(--white)}
.avatar{left:557px;top:2712px;width:82px;height:82px;border-radius:50%;background:radial-gradient(circle at 50% 45%,#d9a58a 0%,#8a5a46 55%,#3a2620 100%);border:4px solid var(--white)}
.quote{left:250px;top:2810px;width:700px;text-align:center;color:var(--white);font-size:14px;line-height:1.75;font-style:italic}
.quote strong{display:block;font-style:normal;font-size:15px;margin-top:16px}
.quote small{font-style:normal;font-size:13px}

/* blog */
.card{top:3234px;width:314px;height:478px;background:var(--white);box-shadow:0 2px 10px rgba(0,0,0,.12)}
.card-photo{position:absolute;left:18px;top:18px;width:278px;height:210px}
.bp1{background:radial-gradient(ellipse 70px 100px at 70px 110px,#e2b89c 0%,rgba(226,184,156,0) 100%),radial-gradient(ellipse 80px 100px at 200px 120px,#2e3a4a 0%,rgba(46,58,74,0) 100%),linear-gradient(160deg,#dfe6ec,#c8ccd2 60%,#9aa6b4)}
.bp2{background:radial-gradient(ellipse 110px 50px at 140px 170px,#1e1e22 0%,rgba(30,30,34,0) 100%),radial-gradient(ellipse 60px 70px at 120px 80px,#d6a888 0%,rgba(214,168,136,0) 100%),linear-gradient(180deg,#9ecae8,#d8ecf6 70%,#b8c4cc)}
.bp3{background:radial-gradient(ellipse 60px 100px at 160px 110px,#8a94a8 0%,rgba(138,148,168,0) 100%),linear-gradient(90deg,#f4ede4,#fbf7f0 50%,#d9cfc2)}
.card-star{position:absolute;right:18px;top:18px;width:40px;height:40px;background:var(--orange);display:flex;align-items:center;justify-content:center}
.card-meta{position:absolute;left:18px;top:252px;width:278px;display:flex;justify-content:space-between;font-size:12px;color:var(--orange)}
.card-meta em{font-style:normal;display:flex;align-items:center;gap:5px}
.card h4{position:absolute;left:18px;top:290px;font-family:"Open Sans",sans-serif;font-weight:700;font-size:18px;color:var(--ink)}
.card p{position:absolute;left:18px;top:326px;width:278px;font-family:"Open Sans",sans-serif;font-size:12px;line-height:1.6;color:var(--text)}
.card-foot{position:absolute;left:18px;top:414px;display:flex;gap:14px;align-items:center}
.share{width:32px;height:30px;background:var(--orange);display:flex;align-items:center;justify-content:center}
.read{border:1px solid var(--orange);color:var(--orange);font-size:11px;padding:7px 10px}

/* contact */
.contact{left:0;top:3820px;width:1200px;height:506px;background:radial-gradient(ellipse 250px 200px at 1080px 250px,#4a4a4a 0%,rgba(74,74,74,0) 100%),linear-gradient(90deg,#262626,#3b3b3b 60%,#2a2a2a)}
.info-card{left:214px;top:3864px;width:254px;height:424px;background:var(--white)}
.info-row{position:absolute;left:48px;font-family:"Open Sans",sans-serif;font-size:14px;color:var(--ink);line-height:1.5}
.info-row strong{font-weight:600}
.info-icon{position:absolute;left:-28px;top:2px}
.touch-box{left:155px;top:4010px;width:272px;height:132px;background:var(--orange);color:var(--white);font-family:"Playfair Display",serif;font-size:44px;line-height:1.05;padding:18px 26px}
.follow{position:absolute;left:22px;top:305px;font-family:"Open Sans",sans-serif;font-weight:700;font-size:14px;color:var(--ink)}
.socials{position:absolute;left:22px;top:336px;display:flex;gap:12px}
.socials span{width:36px;height:36px;border-radius:50%;background:var(--ink)}
.form-panel{left:468px;top:3864px;width:551px;height:424px;background:var(--grey-panel);font-family:"Open Sans",sans-serif;font-size:13px;color:var(--white)}
.field-label{position:absolute}
.field{position:absolute;background:var(--white)}
.submit{position:absolute;left:392px;top:340px;border:1px solid var(--white);padding:10px 14px;font-size:13px;color:var(--white)}
.footer{left:0;top:4326px;width:1200px;height:64px;background:var(--orange);color:var(--white);font-size:13px;text-align:center;line-height:64px}
</style>
</head>
<body>

<header class="abs hero" id="home" role="img" aria-label="Trainer kneeling on a purple yoga mat leaning over a red exercise ball in a sunny grass field"></header>
<nav class="abs navbar">
  <div class="brand"><span class="brand-mark"></span><span>Maren Holt</span></div>
  <div class="nav">
    <a class="active" href="#home">HOME</a>
    <a href="#about">ABOUT ME</a>
    <a href="#services">MY SERVICES</a>
    <a href="#events">EVENTS</a>
    <a href="#blog">BLOG</a>
    <a href="#contact">CONTACTS US</a>
  </div>
</nav>
<p class="abs hero-kicker">IMPROVING THE WORLD'S</p>
<h1 class="abs hero-title">Hi! I'm Maren Holt</h1>
<p class="abs hero-sub">Health and Nutrition Coach. Yoga Teacher.</p>
<a class="abs btn hero-btn" href="#contact">CALL US FREE</a>

<section id="about">
  <div class="abs about-accent"></div>
  <div class="abs about-photo" role="img" aria-label="Woman in a summer outfit standing on a rocky beach by the sea"></div>
  <div class="abs about-text">
    <h2>Living Full Happy Life</h2>
    <h3>Hello! I'm Dummy Text Insert</h3>
    <p>Positive behavioral supports is a behavior management system used to understand what maintains an individual's challenging behavior.</p>
    <p>People's inappropriate behaviors are difficult to change because they are functional. Positive behavioral supports is a behavior management system used to understand what maintains an individual's challenging behavior. People's inappropriate behaviors are difficult to change because they are functional.</p>
    <a class="btn" href="#contact">CALL US FREE</a>
  </div>
</section>

<section id="services">
  <div class="abs features" role="img" aria-label="Orange-tinted background of people training in a gym"></div>
  <h2 class="abs sec-title" style="top:1218px;color:var(--white)">Key Features</h2>
  <div class="abs divider" style="top:1290px;color:var(--white)"><i></i><b></b><i></i></div>

  <div class="abs feature" style="left:100px">
    <div class="feature-icon"><svg width="56" height="56" viewBox="0 0 56 56" fill="none" stroke="#1d1d1d" stroke-width="4" stroke-linecap="round"><path d="M6 10h44M12 10v40M44 10v40M22 10v14M34 10v14"/><circle cx="22" cy="28" r="4"/><circle cx="34" cy="28" r="4"/></svg></div>
    <h4>STREET WORKOUT</h4>
    <p>Lorem Ipsum is simply dummy text of the printing and typesetting industry. Lorem Ipsum has been the industry's</p>
  </div>
  <div class="abs feature" style="left:358px">
    <div class="feature-icon"><svg width="56" height="56" viewBox="0 0 56 56" fill="none" stroke="#1d1d1d" stroke-width="4" stroke-linecap="round" stroke-linejoin="round"><path d="M6 46h40a4 4 0 0 0 0-8H8"/><path d="M42 38L34 10h8"/><path d="M14 30h14M10 22h12"/></svg></div>
    <h4>TREADMILL / CARDIO</h4>
    <p>Lorem Ipsum is simply dummy text of the printing and typesetting industry. Lorem Ipsum has been the industry's</p>
  </div>
  <div class="abs feature" style="left:616px">
    <div class="feature-icon"><svg width="56" height="56" viewBox="0 0 56 56"><rect x="6" y="32" width="34" height="14" rx="2" fill="#1d1d1d"/><circle cx="42" cy="32" r="9" fill="none" stroke="#1d1d1d" stroke-width="4"/><circle cx="42" cy="32" r="3" fill="#1d1d1d"/></svg></div>
    <h4>YOGA / PILATES</h4>
    <p>Lorem Ipsum is simply dummy text of the printing and typesetting industry. Lorem Ipsum has been the industry's</p>
  </div>
  <div class="abs feature" style="left:874px">
    <div class="feature-icon"><svg width="56" height="56" viewBox="0 0 56 56" fill="none" stroke="#1d1d1d" stroke-width="4" stroke-linecap="round"><path d="M6 18c6-6 12 6 18 0s12-6 18 0"/><path d="M6 30c6-6 12 6 18 0s12-6 18 0"/><path d="M6 42c6-6 12 6 18 0s12-6 18 0"/></svg></div>
    <h4>MEDITATION</h4>
    <p>Lorem Ipsum is simply dummy text of the printing and typesetting industry. Lorem Ipsum has been the industry's</p>
  </div>
</section>

<section id="events">
  <h2 class="abs sec-title" style="top:1800px;color:var(--ink)">Our Trainers</h2>
  <div class="abs divider" style="top:1876px;color:var(--ink)"><i></i><b></b><i></i></div>
  <div class="abs trainer-accent"></div>
  <div class="abs trainer-photo tp1" style="left:88px;width:307px" role="img" aria-label="Athlete lifting a dumbbell in a dark gym"></div>
  <div class="abs trainer-photo tp2" style="left:445px;width:310px" role="img" aria-label="Athlete seen from behind holding two dumbbells"></div>
  <div class="abs trainer-photo tp3" style="left:805px;width:310px" role="img" aria-label="Athlete wearing boxing gloves"></div>
  <div class="abs trainer" style="left:88px;width:307px"><h4>Nadia Crowe</h4><span>Vinyasa Yoga</span></div>
  <div class="abs trainer" style="left:445px;width:310px"><h4>Nadia Crowe</h4><span>Vinyasa Yoga</span></div>
  <div class="abs trainer" style="left:805px;width:310px"><h4>Nadia Crowe</h4><span>Vinyasa Yoga</span></div>
</section>

<section>
  <div class="abs testimonials" role="img" aria-label="Orange-tinted background of a gym workout"></div>
  <div class="abs quote-frame"></div>
  <h2 class="abs quote-title">Our Testimonials</h2>
  <div class="abs divider" style="top:2640px;color:var(--white)"><i></i><b></b><i></i></div>
  <div class="abs avatar" role="img" aria-label="Client portrait"></div>
  <p class="abs quote">Lorem Ipsum is simply dummy text of the printing and typesetting industry. Lorem Ipsum has been the industry's standard dummy text ever since the 1500s, when an unknown printer took a galley of type and scrambled it to make a type specimen book.
    <strong>Tom Aldwin</strong><small>Brightside Studio Ltd.</small></p>
</section>

<section id="blog">
  <h2 class="abs sec-title" style="top:3085px;color:var(--ink)">Our Blogs</h2>
  <div class="abs divider" style="top:3160px;color:var(--ink)"><i></i><b></b><i></i></div>

  <article class="abs card" style="left:105px">
    <div class="card-photo bp1" role="img" aria-label="Two people stretching arms during a workout"></div>
    <div class="card-star"><svg width="18" height="18" viewBox="0 0 20 20"><path d="M10 1l2.7 5.8 6.3.7-4.7 4.3 1.3 6.2L10 14.9 4.4 18l1.3-6.2L1 7.5l6.3-.7z" fill="#fff"/></svg></div>
    <div class="card-meta"><span>By admin</span><em><svg width="13" height="12" viewBox="0 0 14 12"><path d="M7 12L1.2 6.2A3.4 3.4 0 0 1 7 1.8a3.4 3.4 0 0 1 5.8 4.4z" fill="#f7941d"/></svg>5</em></div>
    <h4>STICKY BLOG POST</h4>
    <p>Lorem ipsum Proin gravida nibh vel velit auctor aliquet. Aenean sollicitudin, lorem quis bibendum auctor, nisi elit cons...</p>
    <div class="card-foot"><span class="share"><svg width="14" height="14" viewBox="0 0 14 14"><path d="M9 2L3 7l6 5z" fill="#fff"/></svg></span><span class="read">READ MORE</span></div>
  </article>
  <article class="abs card" style="left:439px">
    <div class="card-photo bp2" role="img" aria-label="People riding exercise bikes in a bright gym"></div>
    <div class="card-star"><svg width="18" height="18" viewBox="0 0 20 20"><path d="M10 1l2.7 5.8 6.3.7-4.7 4.3 1.3 6.2L10 14.9 4.4 18l1.3-6.2L1 7.5l6.3-.7z" fill="#fff"/></svg></div>
    <div class="card-meta"><span>By admin</span><em><svg width="13" height="12" viewBox="0 0 14 12"><path d="M7 12L1.2 6.2A3.4 3.4 0 0 1 7 1.8a3.4 3.4 0 0 1 5.8 4.4z" fill="#f7941d"/></svg>10</em></div>
    <h4>IMAGES BLOG POST</h4>
    <p>Lorem ipsum Proin gravida nibh vel velit auctor aliquet. Aenean sollicitudin, lorem quis bibendum auctor, nisi elit cons...</p>
    <div class="card-foot"><span class="share"><svg width="14" height="14" viewBox="0 0 14 14"><path d="M9 2L3 7l6 5z" fill="#fff"/></svg></span><span class="read">READ MORE</span></div>
  </article>
  <article class="abs card" style="left:773px">
    <div class="card-photo bp3" role="img" aria-label="Gym interior with treadmills by tall windows"></div>
    <div class="card-star"><svg width="18" height="18" viewBox="0 0 20 20"><path d="M10 1l2.7 5.8 6.3.7-4.7 4.3 1.3 6.2L10 14.9 4.4 18l1.3-6.2L1 7.5l6.3-.7z" fill="#fff"/></svg></div>
    <div class="card-meta"><span>By admin</span><em><svg width="13" height="12" viewBox="0 0 14 12"><path d="M7 12L1.2 6.2A3.4 3.4 0 0 1 7 1.8a3.4 3.4 0 0 1 5.8 4.4z" fill="#f7941d"/></svg>9</em></div>
    <h4>TEXT BLOG POST</h4>
    <p>Lorem ipsum Proin gravida nibh vel velit auctor aliquet. Aenean sollicitudin, lorem quis bibendum auctor, nisi elit cons...</p>
    <div class="card-foot"><span class="share"><svg width="14" height="14" viewBox="0 0 14 14"><path d="M9 2L3 7l6 5z" fill="#fff"/></svg></span><span class="read">READ MORE</span></div>
  </article>
</section>

<section id="contact">
  <div class="abs contact" role="img" aria-label="Dark background of a gym workout"></div>
  <div class="abs info-card">
    <div class="info-row" style="top:28px">
      <svg class="info-icon" width="18" height="18" viewBox="0 0 18 18"><circle cx="9" cy="9" r="7" fill="none" stroke="#f7941d" stroke-width="2"/><path d="M9 5v4l3 2" stroke="#f7941d" stroke-width="2" fill="none"/></svg>
      <strong>Monday - Friday:</strong><br>9:00 - 6:00</div>
    <div class="info-row" style="top:100px">
      <svg class="info-icon" width="18" height="18" viewBox="0 0 18 18"><path d="M4 2l3 3-2 2c1 2 3 4 5 5l2-2 3 3-2 3C7 15 3 11 2 4z" fill="#f7941d"/></svg>
      <strong>Phone:</strong><br>020 5550 1987</div>
    <div class="follow">Follow Us On</div>
    <div class="socials"><span></span><span></span><span></span><span></span></div>
  </div>
  <div class="abs touch-box">GET IN<br>TOUCH</div>
  <form class="abs form-panel">
    <span class="field-label" style="left:22px;top:60px">Name</span>
    <span class="field" style="left:22px;top:82px;width:238px;height:40px"></span>
    <span class="field-label" style="left:282px;top:60px">Email</span>
    <span class="field" style="left:282px;top:82px;width:238px;height:40px"></span>
    <span class="field-label" style="left:22px;top:148px">Message</span>
    <span class="field" style="left:22px;top:172px;width:498px;height:150px"></span>
    <span class="field" style="left:22px;top:338px;width:14px;height:14px"></span>
    <span class="field-label" style="left:44px;top:336px">Check this box if you are interested in wholesale</span>
    <span class="submit">GET IN TOUCH</span>
  </form>
</section>

<footer class="abs footer">Copyright 2017 by Maren Holt Personal Training. All Rights Reserved.</footer>

</body>
</html>
```